New business card/stationary for a consulting company

I am looking for a clean and very professional looking business card for my consulting company as well as corresponding stationary. I am uploading our logo. I like simple and powerful for the feel. No graphics but I am open on everything else. Below is my contact information but would like the final to be in a version I can add my employees information into and print. Thank you.

Daniel Whitcombe
dan@ferncliffadvisory.com
2870 North 9th Avenue, Summit Floor, Elm Ridge, Illinois 60531
www.ferncliffadvisory.com

Industry/Entity Type

Consulting

Contact Information for Business Card

Daniel Whitcombe
dan@ferncliffadvisory.com
www.ferncliffadvisory.com

Font styles to use
Serif
Sans Serif

Requirements
Must have
• Our logo and the business card details.
Nice to have
• our website www.ferncliffadvisory.com

```html
<!DOCTYPE html>
<html lang="en">
<head>
<meta charset="utf-8">
<title>Ferncliff Advisory — Business Card</title>
<link href="https://fonts.googleapis.com/css2?family=Montserrat:wght@300;400;500;700&display=swap" rel="stylesheet">
<style>
  :root {
    --navy: #0c0f6e;
    --navy-deep: #0a0c5c;
    --paper: #ffffff;
    --ink: #2b2b33;
    --backdrop: #e6e6e8;
  }
  * { box-sizing: border-box; margin: 0; padding: 0; }
  html, body {
    width: 1200px; height: 1022px; overflow: hidden;
    background: var(--backdrop);
    font-family: "Montserrat", sans-serif;
  }
  .card {
    position: absolute;
    width: 620px; height: 354px;
    border-radius: 4px;
    overflow: hidden;
    box-shadow: 0 6px 18px rgba(0,0,0,0.18);
  }
  /* Front face */
  .card--front {
    left: 110px; top: 90px;
    background: linear-gradient(135deg, var(--navy) 0%, var(--navy-deep) 100%);
    color: var(--paper);
  }
  .wordmark {
    display: flex; align-items: center; justify-content: center; gap: 14px;
  }
  .wordmark__mark { width: 22px; height: 22px; }
  .wordmark__name {
    font-weight: 400; letter-spacing: 0.04em; text-transform: uppercase;
  }
  .card--front .wordmark {
    position: absolute; left: 0; right: 0; top: 120px;
  }
  .card--front .wordmark__mark { background: var(--paper); }
  .card--front .wordmark__name { font-size: 34px; color: var(--paper); }
  .front__rule {
    position: absolute; left: 300px; right: 40px; top: 182px;
    height: 1.5px; background: var(--paper);
  }
  .front__web {
    position: absolute; left: 40px; right: 40px; bottom: 60px;
    display: flex; align-items: center; gap: 14px;
    font-size: 13px; font-weight: 700;
  }
  .front__web::before, .front__web::after {
    content: ""; flex: 1; height: 1.5px; background: var(--paper);
  }
  /* Back face */
  .card--back {
    left: 470px; top: 560px;
    background: var(--paper);
    color: var(--ink);
  }
  .card--back .wordmark { position: absolute; left: 0; right: 0; top: 58px; }
  .card--back .wordmark__mark { background: var(--navy); }
  .card--back .wordmark__name { font-size: 28px; color: var(--navy); }
  .back__body {
    position: absolute; left: 0; right: 0; top: 150px;
    display: flex; justify-content: center; align-items: stretch; gap: 26px;
  }
  .person { text-align: right; }
  .person__name { font-size: 19px; font-weight: 700; color: var(--navy); }
  .person__role { font-size: 11px; font-weight: 700; color: var(--navy); margin-top: 4px; }
  .person__address { font-size: 12.5px; line-height: 1.9; margin-top: 8px; }
  .divider { width: 1.5px; background: var(--navy); }
  .contacts { list-style: none; font-size: 12.5px; }
  .contacts li { display: flex; align-items: center; gap: 10px; line-height: 1.95; }
  .contacts svg { width: 12px; height: 12px; fill: var(--navy); flex: none; }
  .back__band {
    position: absolute; left: 0; right: 0; bottom: 0; height: 22px;
    background: var(--navy);
  }
</style>
</head>
<body>
  <section class="card card--front" aria-label="Card front">
    <div class="wordmark">
      <span class="wordmark__mark"></span>
      <span class="wordmark__name">Ferncliff Advisory</span>
    </div>
    <div class="front__rule"></div>
    <div class="front__web">www.ferncliffadvisory.com</div>
  </section>

  <section class="card card--back" aria-label="Card back">
    <div class="wordmark">
      <span class="wordmark__mark"></span>
      <span class="wordmark__name">Ferncliff Advisory</span>
    </div>
    <div class="back__body">
      <div class="person">
        <p class="person__name">Daniel Whitcombe</p>
        <p class="person__role">Founder/CEO</p>
        <p class="person__address">2870 North 9th Avenue, Summit Floor,<br>Elm Ridge, Illinois 60531</p>
      </div>
      <div class="divider"></div>
      <ul class="contacts">
        <li><svg viewBox="0 0 24 24"><path d="M6.6 10.8a15.1 15.1 0 0 0 6.6 6.6l2.2-2.2a1 1 0 0 1 1-.25 11.4 11.4 0 0 0 3.6.57 1 1 0 0 1 1 1V20a1 1 0 0 1-1 1A17 17 0 0 1 3 4a1 1 0 0 1 1-1h3.5a1 1 0 0 1 1 1c0 1.25.2 2.45.57 3.57a1 1 0 0 1-.25 1z"/></svg>(855) 302 71846</li>
        <li><svg viewBox="0 0 24 24"><path d="M7 1h10a2 2 0 0 1 2 2v18a2 2 0 0 1-2 2H7a2 2 0 0 1-2-2V3a2 2 0 0 1 2-2zm0 3v14h10V4zm5 15.5a1 1 0 1 0 0 2 1 1 0 0 0 0-2z"/></svg>+918760241953</li>
        <li><svg viewBox="0 0 24 24"><path d="M2 5h20v14H2zm2 2v.4l8 5 8-5V7zm0 2.8V17h16V9.8l-8 5z"/></svg>dan@ferncliffadvisory.com</li>
        <li><svg viewBox="0 0 24 24"><path d="M12 2a10 10 0 1 0 0 20 10 10 0 0 0 0-20zm6.9 9h-3a15 15 0 0 0-1.3-5.6A8 8 0 0 1 18.9 11zM12 4.1c.9 1.3 1.8 3.6 1.9 6.9h-3.8c.1-3.3 1-5.6 1.9-6.9zM9.4 5.4A15 15 0 0 0 8.1 11h-3a8 8 0 0 1 4.3-5.6zM5.1 13h3a15 15 0 0 0 1.3 5.6A8 8 0 0 1 5.1 13zm6.9 6.9c-.9-1.3-1.8-3.6-1.9-6.9h3.8c-.1 3.3-1 5.6-1.9 6.9zm2.6-1.3a15 15 0 0 0 1.3-5.6h3a8 8 0 0 1-4.3 5.6z"/></svg>www.ferncliffadvisory.com</li>
      </ul>
    </div>
    <div class="back__band"></div>
  </section>
</body>
</html>
```